Velundra Jobs portal

Velundra Jobs is a job portal connecting job seekers and companies offering part time jobs in the Mena region, starting in the UAE. We would like to see designs that use the color blue. We have attached images to give an idea what the website should look like. When a company posts a job the job seekers are not allowed to see which company has posted a job. There should also be a coinvex gateway. On the landing page we want a catching picture that we will send.

Target Market(s)

Students and promotional workers

Logo Text

Velundra Jobs

Coding

Coded - Design and coding required

Number of Pages Required

4 page

Font styles to use
Sans Serif

Colors
33a6d7
0692cd
85cae6

```html
<!DOCTYPE html>
<html lang="en">
<head>
<meta charset="utf-8">
<title>Velundra Jobs</title>
<link href="https://fonts.googleapis.com/css2?family=Open+Sans:wght@400;600;700&display=swap" rel="stylesheet">
<style>
:root{
  --teal:#40a9a9;
  --teal-dark:#2f9696;
  --navy:#2a5ea8;
  --pink:#e5468a;
  --text:#555;
  --muted:#777;
  --line:#d9d9d9;
  --row:#eeeeee;
  --footer:#333;
  --c1:#e84c3d;--c2:#f58a42;--c3:#f9b233;--c4:#17b08c;--c5:#1ebfc9;
  --c6:#2e9ad7;--c7:#2573b6;--c8:#7a4cbe;--c9:#c2387a;--c10:#e4508a;
}
*{box-sizing:border-box;margin:0;padding:0}
html,body{width:1200px;height:867px;overflow:hidden;background:#fff;font-family:"Open Sans",sans-serif;color:var(--text)}
.page{position:relative;width:1200px;height:867px}
.header{position:absolute;left:0;top:0;width:1200px;height:75px;border-bottom:1px solid var(--line)}
.logo{position:absolute;left:99px;top:14px;font-size:36px;font-weight:400;color:var(--teal);letter-spacing:-.5px}
.nav{position:absolute;top:32px;font-size:12px;color:#555}
.nav.about{left:297px}.nav.contact{left:396px}
.circle{position:absolute;border-radius:50%;display:flex;align-items:center;justify-content:center}
.search{left:875px;top:19px;width:38px;height:38px;background:var(--teal)}
.bell{left:927px;top:19px;width:38px;height:38px;background:var(--pink)}
.badge{left:951px;top:8px;width:22px;height:22px;background:#8a6fd1;color:#fff;font-size:11px;border:2px solid #fff}
.avatar{left:983px;top:14px;width:48px;height:48px;background:linear-gradient(#c9b39a,#8a6f5a);border:2px solid #ddd}
.logout{position:absolute;left:1041px;top:32px;font-size:12px;color:#555}
.sidebar{position:absolute;left:99px;top:97px;width:218px;border:1px solid var(--line);border-left:0;background:#f4f4f4}
.cat{display:flex;height:38.6px;border-bottom:1px solid var(--line);align-items:center;font-size:12px}
.cat:last-child{border-bottom:0}
.cat .ico{width:38.6px;height:100%;display:flex;align-items:center;justify-content:center}
.cat .name{flex:1;padding-left:13px;color:#666}
.cat .count{padding-right:15px;font-size:11px}
.mascot{position:absolute;left:81px;top:510px;width:228px;height:300px;border-radius:40% 40% 30% 30%;background:radial-gradient(circle at 50% 40%,#dde6f3,#f4e6ef 60%,#fff 80%);opacity:.8}
.filter{position:absolute;left:353px;top:97px;width:749px;height:65px;border:1px solid var(--line)}
.field{position:absolute;top:15px;height:33px;border:1px solid #ccc;font-size:12px;padding:9px 14px;color:#555}
.field.keyword{left:18px;width:270px}
.field.district{left:301px;width:270px}
.field.district svg{position:absolute;right:12px;top:13px}
.btn-filter{position:absolute;left:582px;top:14px;width:152px;height:34px;background:var(--teal);color:#fff;font-size:13px;display:flex;align-items:center;justify-content:center}
.jobs{position:absolute;left:353px;top:183px;width:749px;border-collapse:collapse}
.jobs th{background:var(--navy);color:#fff;font-weight:400;font-size:13px;text-align:left;height:40px;padding-left:20px;border-right:1px solid #fff}
.jobs th:last-child{border-right:0}
.jobs td{height:55.7px;background:var(--row);border:1px solid var(--line);font-size:12px;color:#666;padding-left:20px;position:relative}
.jobs td.title{font-size:15px;font-weight:700;color:var(--teal);width:228px}
.jobs td.date{width:222px;padding-left:16px}
.jobs td.prov{padding-left:16px}
.jobs tr.active td{background:var(--teal);color:#fff;border-color:#5bb7b7}
.apply{position:absolute;right:12px;top:12px;width:106px;height:30px;background:var(--teal);color:#fff;font-size:12px;display:flex;align-items:center;justify-content:center}
tr.active .apply{background:transparent;border:1px solid #fff}
.featured-title{position:absolute;left:356px;top:473px;font-size:17px;font-weight:700;color:var(--pink)}
.providers{position:absolute;left:353px;top:519px;width:749px;height:232px;background:#efefef;border:1px solid var(--line)}
.card{position:absolute;top:20px;width:127px;text-align:center}
.card .frame{height:141px;border:1px solid #ccc;background:#fff;padding:5px}
.card .photo{width:100%;height:100%}
.card .name{margin-top:9px;font-size:12px;font-weight:600;color:#444}
.card .age{margin-top:4px;font-size:12px;color:#444}
.footer{position:absolute;left:0;top:819px;width:1200px;height:48px;background:var(--footer);color:#9a9a9a;font-size:12px}
.footer .copy{position:absolute;left:101px;top:16px}
.footer .links{position:absolute;right:99px;top:16px;word-spacing:2px}
.footer .sep{margin:0 16px}
</style>
</head>
<body>
<div class="page">
  <header class="header">
    <div class="logo">velundra</div>
    <span class="nav about">About Us</span>
    <span class="nav contact">Contact us</span>
    <div class="circle search"><svg width="15" height="15" viewBox="0 0 16 16"><circle cx="6.5" cy="6.5" r="5" fill="none" stroke="#fff" stroke-width="2"/><line x1="10.5" y1="10.5" x2="14.5" y2="14.5" stroke="#fff" stroke-width="2.2"/></svg></div>
    <div class="circle bell"><svg width="15" height="16" viewBox="0 0 16 16"><path d="M8 2c-3 0-4.5 2.2-4.5 5v3L2 12h12l-1.5-2V7C12.5 4.2 11 2 8 2z" fill="none" stroke="#fff" stroke-width="1.6"/><path d="M6 13.5a2 2 0 004 0" fill="none" stroke="#fff" stroke-width="1.5"/></svg></div>
    <div class="circle badge">22</div>
    <div class="circle avatar" role="img" aria-label="User profile photo"></div>
    <span class="logout">Log Out <svg width="9" height="6" viewBox="0 0 9 6"><path d="M1 1l3.5 3.5L8 1" fill="none" stroke="#666" stroke-width="1.3"/></svg></span>
  </header>

  <nav class="sidebar">
    <div class="cat"><div class="ico" style="background:var(--c1)"><svg width="14" height="12"><path d="M1 4h3l7-3v10L4 8H1z" fill="#fff"/></svg></div><span class="name">Category 1</span><span class="count" style="color:var(--c1)">( 33 )</span></div>
    <div class="cat"><div class="ico" style="background:var(--c2)"><svg width="12" height="14"><rect x="1" y="1" width="10" height="12" fill="none" stroke="#fff" stroke-width="1.4"/><path d="M3 5h6M3 8h6M3 11h4" stroke="#fff"/></svg></div><span class="name">Category 2</span><span class="count" style="color:var(--c2)">( 3 )</span></div>
    <div class="cat"><div class="ico" style="background:var(--c3)"><svg width="16" height="12"><path d="M8 1L1 4l7 3 7-3zM4 6v3c2 2 6 2 8 0V6L8 8z" fill="#fff"/></svg></div><span class="name">Category 3</span><span class="count" style="color:var(--c3)">( 23 )</span></div>
    <div class="cat"><div class="ico" style="background:var(--c4)"><svg width="14" height="14"><circle cx="7" cy="7" r="5" fill="none" stroke="#fff" stroke-width="3" stroke-dasharray="2.5 1.4"/><circle cx="7" cy="7" r="2" fill="#fff"/></svg></div><span class="name">Category 4</span><span class="count" style="color:var(--c4)">( 13 )</span></div>
    <div class="cat"><div class="ico" style="background:var(--c5)"><svg width="14" height="14"><circle cx="4.5" cy="4.5" r="3" fill="none" stroke="#fff" stroke-width="1.6"/><circle cx="9.5" cy="9.5" r="3" fill="none" stroke="#fff" stroke-width="1.6"/></svg></div><span class="name">Category 5</span><span class="count" style="color:var(--c5)">( 33 )</span></div>
    <div class="cat"><div class="ico" style="background:var(--c6)"><svg width="10" height="14"><rect x="3" y="1" width="4" height="8" rx="2" fill="#fff"/><path d="M1 7a4 4 0 008 0M5 11v2" fill="none" stroke="#fff" stroke-width="1.3"/></svg></div><span class="name">Category 6</span><span class="count" style="color:var(--c6)">( 43 )</span></div>
    <div class="cat"><div class="ico" style="background:var(--c7)"><svg width="14" height="14"><path d="M13 1L1 7l4 1 1 5 2-3 3 2z" fill="#fff"/></svg></div><span class="name">Category 7</span><span class="count" style="color:var(--c7)">( 13 )</span></div>
    <div class="cat"><div class="ico" style="background:var(--c8)"><svg width="14" height="14"><path d="M3 4a5 5 0 11-1 4" fill="none" stroke="#fff" stroke-width="2"/><path d="M1 1v4h4z" fill="#fff"/></svg></div><span class="name">Category 8</span><span class="count" style="color:var(--c8)">( 189 )</span></div>
    <div class="cat"><div class="ico" style="background:var(--c9)"><svg width="14" height="12"><rect x="1" y="9" width="2" height="2" fill="#fff"/><rect x="4" y="7" width="2" height="4" fill="#fff"/><rect x="7" y="4" width="2" height="7" fill="#fff"/><rect x="10" y="1" width="2" height="10" fill="#fff"/></svg></div><span class="name">Category 9</span><span class="count" style="color:var(--c9)">( 983 )</span></div>
    <div class="cat"><div class="ico" style="background:var(--c10)"><svg width="12" height="14"><circle cx="6" cy="4" r="3" fill="#fff"/><path d="M1 13a5 5 0 0110 0z" fill="#fff"/></svg></div><span class="name">Category 10</span><span class="count" style="color:var(--c10)">( 23 )</span></div>
  </nav>

  <div class="mascot" role="img" aria-label="Faint mascot illustration in pastel blue and pink"></div>

  <section class="filter">
    <div class="field keyword">Keyword</div>
    <div class="field district">District 1<svg width="9" height="6" viewBox="0 0 9 6"><path d="M1 1l3.5 3.5L8 1" fill="none" stroke="#555" stroke-width="1.3"/></svg></div>
    <div class="btn-filter">Filter Jobs</div>
  </section>

  <table class="jobs">
    <thead><tr><th>Job Tittle</th><th style="padding-left:16px">Due Date</th><th style="padding-left:16px">Provider Name</th></tr></thead>
    <tbody>
      <tr class="active"><td class="title">Job tittle number 1</td><td class="date">Due date: 23 jan 2105</td><td class="prov">Provider 1<span class="apply">Apply Now</span></td></tr>
      <tr><td class="title">Job tittle number 1</td><td class="date">Due date: 23 jan 2105</td><td class="prov">Provider 1<span class="apply">Apply Now</span></td></tr>
      <tr><td class="title">Job tittle number 1</td><td class="date">Due date: 23 jan 2105</td><td class="prov">Provider 1<span class="apply">Apply Now</span></td></tr>
      <tr><td class="title">Job tittle number 1</td><td class="date">Due date: 23 jan 2105</td><td class="prov">Provider 1<span class="apply">Apply Now</span></td></tr>
    </tbody>
  </table>

  <h2 class="featured-title">Featured job Providers</h2>
  <section class="providers">
    <div class="card" style="left:21px"><div class="frame"><div class="photo" role="img" aria-label="Provider portrait photo" style="background:linear-gradient(#e8ece8,#2aa6c9)"></div></div><div class="name">Loren Kadis</div><div class="age">Age : 22 years</div></div>
    <div class="card" style="left:166px"><div class="frame"><div class="photo" role="img" aria-label="Provider portrait photo" style="background:linear-gradient(135deg,#9fc36a,#5a3a2a)"></div></div><div class="name">Loren Kadis</div><div class="age">Age : 22 years</div></div>
    <div class="card" style="left:311px"><div class="frame"><div class="photo" role="img" aria-label="Provider portrait photo" style="background:linear-gradient(#8cb064,#3b3a36)"></div></div><div class="name">Loren Kadis</div><div class="age">Age : 22 years</div></div>
    <div class="card" style="left:456px"><div class="frame"><div class="photo" role="img" aria-label="Provider portrait photo" style="background:linear-gradient(#c9cfd6,#b08b6a)"></div></div><div class="name">Loren Kadis</div><div class="age">Age : 22 years</div></div>
    <div class="card" style="left:601px"><div class="frame"><div class="photo" role="img" aria-label="Provider portrait photo" style="background:linear-gradient(#5f8a3c,#9aa9c4)"></div></div><div class="name">Loren Kadis</div><div class="age">Age : 22 years</div></div>
  </section>

  <footer class="footer">
    <span class="copy">© Copyrights. 2015. Velundra. All rights reserved.</span>
    <span class="links">About Us<span class="sep">/</span>Terms &amp; Conditions<span class="sep">/</span>Sitemap</span>
  </footer>
</div>
</body>
</html>
```